email presentation and marketing

we need a email to be used to present our company and services to potential customer. it needs to contain our logo, address, details about our company, photos and a well described text about our work .
I will send a web site from one of the company we are targeting.
The e mail must be sober, elegant, persuasive. The client needs to have the feeling it is dealing to a big company.
See below one of out potential clients
http://qrvdwellings.com/

Target Market(s)

High end custom homes

Industry/Entity Type

Painting And Decorating

Font styles to use
Serif
Sans Serif

Requirements
Must have
• Our name, location, portfolio (need to send some pics), web site http://kb-coatingworks.com.
• Need to develop a email to present our company to potential clients.
Nice to have
• clients reviews.
• we are listed on nest ratings. https://nestratings.com/companies/5831046-kb-custom?service_area=7420561
Should not have
• not colorful

```html
<!DOCTYPE html>
<html lang="en">
<head>
<meta charset="utf-8">
<title>KB Coating Works – Custom Home Specialists</title>
<link href="https://fonts.googleapis.com/css2?family=Montserrat:wght@500;600;700;800&family=Open+Sans:wght@400;600;700&display=swap" rel="stylesheet">
<style>
:root{
  --gold:#f2c53d;
  --ink:#161616;
  --charcoal:#4a4a4a;
  --paper:#ffffff;
  --mist:#e9e9e9;
  --mist-light:#f3f3f3;
  --text:#333333;
  --muted:#6b6b6b;
  --link:#2fa6e0;
  --badge:#6a6a6a;
}
*{box-sizing:border-box;margin:0;padding:0}
html,body{width:1200px;height:5084px;overflow:hidden}
body{background:var(--paper);font-family:"Open Sans",Arial,sans-serif;color:var(--text)}
.email{width:1200px;height:5084px;position:relative}
.preheader{height:68px;background:var(--mist);display:flex;align-items:center;justify-content:center;font-size:20px;color:var(--muted)}
.preheader a{color:var(--muted);margin-left:8px}
.hero-photo{height:652px;background:linear-gradient(180deg,#9ea4aa 0%,#c9cdd1 35%,#6d6a66 62%,#e4e6e8 100%)}
.brand-band{height:180px;background:var(--ink);display:flex;align-items:center;padding-left:170px;gap:40px}
.brand-mark{width:150px;height:130px;display:flex;align-items:center;justify-content:center;gap:14px}
.brand-mark .square{width:22px;height:22px;background:var(--gold)}
.brand-mark .name{font-family:"Montserrat",Arial,sans-serif;font-weight:800;font-size:54px;color:var(--gold)}
.brand-copy{font-family:"Montserrat",Arial,sans-serif;line-height:1.2}
.brand-copy .title{color:var(--gold);font-weight:700;font-size:46px;letter-spacing:1px}
.brand-copy .tag{color:#fff;font-weight:600;font-size:30px;letter-spacing:1px}
.brand-copy .city{color:#fff;font-weight:600;font-size:26px;letter-spacing:2px}
.section-title{height:80px;display:flex;align-items:center;justify-content:center;font-family:"Montserrat",Arial,sans-serif;font-weight:700;font-size:40px;color:var(--ink);letter-spacing:1px;background:var(--mist)}
.services{background:var(--mist);padding-top:12px}
.service{display:flex;align-items:flex-start;padding:0 120px;margin-bottom:32px}
.service.light{background:var(--mist-light)}
.service .photo{flex:0 0 440px;border:8px solid #fff;box-shadow:0 2px 6px rgba(0,0,0,.15)}
.service .copy{font-size:19px;line-height:1.55;color:var(--text)}
.service h3{font-family:"Montserrat",Arial,sans-serif;font-weight:700;font-size:26px;color:var(--ink);margin-bottom:18px;letter-spacing:.5px}
.service p{margin-bottom:22px}
.btn{display:inline-block;background:var(--gold);color:var(--ink);font-family:"Montserrat",Arial,sans-serif;font-weight:600;font-size:18px;padding:10px 24px;text-decoration:none}
.drywall{height:308px;padding-top:28px}
.drywall .copy{margin-left:68px;padding-top:8px;width:450px}
.drywall .photo{height:252px;background:linear-gradient(135deg,#f4f4f4,#d9d9d9 60%,#bfbfbf)}
.staircase{height:488px;padding-top:38px}
.staircase .copy{width:470px;margin-right:50px}
.staircase .photo{height:432px;background:linear-gradient(160deg,#f1eeea 0%,#c9b9a5 45%,#6b4a33 100%)}
.wallpaper{height:340px;padding-top:28px}
.wallpaper .copy{margin-left:58px;width:460px}
.wallpaper .photo{height:292px;background:linear-gradient(135deg,#d7d4d1,#8d8884 50%,#4a4644)}
.spray{height:608px;padding-top:48px;margin-bottom:0}
.spray .copy{width:470px;margin-right:50px}
.spray .photo{height:520px;background:linear-gradient(135deg,#efefef 0%,#d4d4d4 50%,#f6f6f6 70%,#a8a8a8 100%);border-color:#1a1a1a}
.spray .btn{margin-top:40px}
.why-band{height:188px;position:relative;background:var(--gold);margin-top:20px}
.why-band svg.wedge{position:absolute;left:0;top:0}
.why-title{position:absolute;left:140px;top:38px;font-family:"Montserrat",Arial,sans-serif;font-weight:800;font-size:38px;line-height:1.05;color:var(--gold)}
.why-list{position:absolute;left:470px;top:36px;display:grid;grid-template-columns:320px 320px;row-gap:38px;list-style:none}
.why-list li{font-family:"Montserrat",Arial,sans-serif;font-weight:700;font-size:26px;color:var(--ink);display:flex;align-items:center;gap:22px}
.why-list li::before{content:"";width:20px;height:20px;border-radius:50%;background:var(--ink)}
.works{background:var(--mist);height:720px}
.works .section-title{height:112px;padding-top:20px}
.works-grid{display:grid;grid-template-columns:repeat(3,280px);column-gap:52px;row-gap:36px;padding:0 120px}
.works-grid .photo{height:252px;border:8px solid #fff;box-shadow:0 2px 6px rgba(0,0,0,.15)}
.w1{background:linear-gradient(135deg,#f3f3f1,#cfcac3)}
.w2{background:linear-gradient(160deg,#efefef,#8a8a8a 55%,#3b3b3b)}
.w3{background:linear-gradient(135deg,#7a5a44,#e9e4de 50%,#5b4536)}
.w4{background:linear-gradient(135deg,#e8e6e2,#383634 55%,#cfcac3)}
.w5{background:linear-gradient(180deg,#dcdcdc,#f7f7f7 50%,#a9a39c)}
.w6{background:linear-gradient(180deg,#f4f0ea,#cdb79c 50%,#8d7a62)}
.reviews{height:852px;background:var(--charcoal);padding-top:40px;text-align:center;color:#fff}
.listing-badge{display:block;width:200px;height:80px;margin:0 auto 68px;background:var(--badge)}
.review{width:760px;margin:0 auto;padding-bottom:38px;margin-bottom:38px;border-bottom:1px solid #6a6a6a}
.review:last-child{border-bottom:none}
.review blockquote{font-size:21px;line-height:1.5;margin-bottom:22px}
.review cite{font-style:normal;font-family:"Montserrat",Arial,sans-serif;font-weight:700;font-size:20px;color:var(--link)}
.review cite.caps{text-transform:uppercase}
.social{height:260px;display:flex;align-items:center;justify-content:center;gap:32px}
.social span{width:76px;height:76px;border-radius:50%;background:var(--gold)}
.contact-bar{height:160px;background:var(--ink);color:#fff;display:flex;padding:30px 0 0 120px;font-size:20px;line-height:1.6}
.contact-bar .address{width:440px;display:flex;gap:26px}
.contact-bar .lines{display:flex;flex-direction:column;gap:8px}
.contact-bar .row{display:flex;align-items:center;gap:22px}
.legal{height:76px;display:flex;align-items:center;justify-content:center;font-size:19px;color:var(--text)}
.legal a{color:var(--text);margin:0 12px}
</style>
</head>
<body>
<div class="email">
  <div class="preheader">Don't see this email properly? <a href="#">View in web browser</a></div>
  <div class="hero-photo" role="img" aria-label="Large stone custom home in winter snow under an overcast sky"></div>
  <header class="brand-band">
    <div class="brand-mark"><span class="square"></span><span class="name">KB</span></div>
    <div class="brand-copy">
      <div class="title">KB COATING WORKS</div>
      <div class="tag">CUSTOM HOME SPECIALISTS</div>
      <div class="city">TORONTO</div>
    </div>
  </header>

  <h2 class="section-title">OUR SERVICES</h2>
  <section class="services">
    <div class="service drywall light">
      <div class="photo" role="img" aria-label="Painter repairing a curved drywall ceiling"></div>
      <div class="copy">
        <h3>DRYWALL REPAIRS</h3>
        <p>For your convenience, we offer drywall repair as one of our services. Contact us now and get your free estimate.</p>
        <a class="btn" href="#">Get Free Quote</a>
      </div>
    </div>
    <div class="service staircase">
      <div class="copy">
        <h3>STAIRCASE FINISH</h3>
        <p>We are definitely the right company to help you! We take details very serious, and your staircase requires care and attention. Perfection is our duty.</p>
        <p>and your satisfaction our goal. You are welcome to checkout some of our work through our pictures</p>
        <a class="btn" href="#">Get Free Quote</a>
      </div>
      <div class="photo" role="img" aria-label="Curved staircase with wrought iron railing and wooden handrail"></div>
    </div>
    <div class="service wallpaper light">
      <div class="photo" role="img" aria-label="Bedroom with patterned feature wallpaper"></div>
      <div class="copy">
        <h3>WALLPAPER INSTALLATION</h3>
        <p>If you would like to give your house/business that special touch, wallpaper may be just what you are looking for. Our employees are specialist in removing and applying wallpaper. Give us a call today and ask for your quote!</p>
        <a class="btn" href="#">Get Free Quote</a>
      </div>
    </div>
    <div class="service spray">
      <div class="copy">
        <h3>SPRAY FINISH</h3>
        <p>High end finish? Spray finish is what you need!</p>
        <p>We, at KB Coating Works, are compromised to provide our clients with a high end finish for all our painting projects. The best way to make that happen, is by using the best equipment in the market.</p>
        <p>We have the right skills and the best equipment to provide you with an amazing and smooth finish.</p>
        <a class="btn" href="#">Get Free Quote</a>
      </div>
      <div class="photo" role="img" aria-label="Glossy marble-look spray-finished wall panel"></div>
    </div>
  </section>

  <section class="why-band">
    <svg class="wedge" width="470" height="188" viewBox="0 0 470 188"><polygon points="0,0 400,0 460,94 400,188 0,188" fill="#161616"/></svg>
    <div class="why-title">WHY<br>CHOOSE<br>US?</div>
    <ul class="why-list">
      <li>Available Now</li>
      <li>Best Price</li>
      <li>Professional Work</li>
      <li>Free Estimation</li>
    </ul>
  </section>

  <section class="works">
    <h2 class="section-title">OUR WORKS</h2>
    <div class="works-grid">
      <div class="photo w1" role="img" aria-label="Bright white living room interior"></div>
      <div class="photo w2" role="img" aria-label="Spiral staircase with dark railing"></div>
      <div class="photo w3" role="img" aria-label="Wood-trimmed wall with built-in fireplace"></div>
      <div class="photo w4" role="img" aria-label="Entry hall with dark arched doorway"></div>
      <div class="photo w5" role="img" aria-label="Bathroom with freestanding tub under tall windows"></div>
      <div class="photo w6" role="img" aria-label="Domed ceiling with chandelier"></div>
    </div>
  </section>

  <section class="reviews">
    <div class="listing-badge" role="img" aria-label="Nest Ratings listing badge"></div>
    <div class="review">
      <blockquote>"Contractor was hired to paint New home. Staff was friendly, courteous, helpful, clean, proactive, reliable."</blockquote>
      <cite>Paint &amp; Wallpaper Contractors</cite>
    </div>
    <div class="review">
      <blockquote>"Kevin and his staff are realible, provide great quality and service. myself and my clients are extremely satisfied with his work."</blockquote>
      <cite class="caps">Paint of new homes and renovations</cite>
    </div>
    <div class="review">
      <blockquote>"Behaviour and attitude is good . He is very good with spray painting. Definitely I will work with him again."</blockquote>
      <cite>Custom Home Painting</cite>
    </div>
  </section>

  <nav class="social" aria-label="Social links"><span></span><span></span><span></span><span></span><span></span><span></span></nav>

  <footer class="contact-bar">
    <div class="address">
      <svg width="22" height="30" viewBox="0 0 22 30"><path d="M11 0a11 11 0 0 0-11 11c0 8 11 19 11 19s11-11 11-19A11 11 0 0 0 11 0zm0 15a4 4 0 1 1 0-8 4 4 0 0 1 0 8z" fill="#f2c53d"/></svg>
      <div>412 Alderbrook Ave, Unit C3<br>M4K 2R7<br>Toronto | Ontario</div>
    </div>
    <div class="lines">
      <div class="row"><svg width="24" height="24" viewBox="0 0 24 24"><path d="M6.6 10.8a15 15 0 0 0 6.6 6.6l2.2-2.2a1 1 0 0 1 1-.25 11.4 11.4 0 0 0 3.6.57 1 1 0 0 1 1 1V20a1 1 0 0 1-1 1A17 17 0 0 1 3 4a1 1 0 0 1 1-1h3.5a1 1 0 0 1 1 1c0 1.25.2 2.45.57 3.57a1 1 0 0 1-.25 1z" fill="#f2c53d"/></svg>647 555 0182</div>
      <div class="row"><svg width="24" height="24" viewBox="0 0 24 24"><path d="M2 5h20v14H2z" fill="#f2c53d"/><path d="M2 5l10 8 10-8" fill="none" stroke="#161616" stroke-width="2"/></svg>info@kbcoatingpros.com</div>
      <div class="row"><svg width="24" height="24" viewBox="0 0 24 24"><circle cx="12" cy="12" r="10" fill="#f2c53d"/><path d="M2 12h20M12 2c3 3 3 17 0 20M12 2c-3 3-3 17 0 20" fill="none" stroke="#161616" stroke-width="1.5"/></svg>www.kbcoatingpros.com</div>
    </div>
  </footer>

  <div class="legal"><a href="#">Unsubscribe</a> newsletter &nbsp;| <a href="#">Update</a> your preference</div>
</div>
</body>
</html>
```